Harbor Ridge Painting Epoxy Flyer

We need a promotional flyer for a new epoxy floor coatings division of our painting company. We do epoxy garage floor coatings and paver sealing. It needs to be based on and very similar to the attached flyer. The garage floor picture needs to look more realistic, and the before and after pavers pictures should look less shiny but still a good contrast. Include attached logo

```html
<!DOCTYPE html>
<html lang="en">
<head>
<meta charset="utf-8">
<title>Harbor Ridge Painting – Garage &amp; Driveway Flyer</title>
<link rel="stylesheet" href="https://fonts.googleapis.com/css2?family=Poppins:wght@400;500;600;700;800&family=Syne:wght@800&display=swap">
<style>
  :root {
    --orange: #d2520d;
    --orange-frame: #e0580c;
    --green: #4cb843;
    --blue: #2aa6e0;
    --ink: #141414;
    --rule: #b9b9b9;
    --paper: #ffffff;
    --garage-1: #cfcdc7;
    --garage-2: #6f6c63;
    --room-1: #ecebe7;
    --room-2: #8a7461;
    --room-3: #e6e3dc;
    --room-4: #6b5b4c;
  }
  * { box-sizing: border-box; margin: 0; padding: 0; }
  html, body { width: 1043px; height: 1200px; overflow: hidden; }
  body { background: var(--paper); font-family: "Poppins", sans-serif; color: var(--ink); position: relative; }
  .abs { position: absolute; }

  .photo-frame { position: absolute; border: 5px solid var(--orange-frame); border-radius: 8px; overflow: hidden; }
  .photo { width: 100%; height: 100%; }
  .photo.garage-before { background: linear-gradient(180deg, var(--garage-1) 0%, #e9e8e3 45%, #8b887e 60%, var(--garage-2) 100%); }
  .photo.garage-after { background: linear-gradient(180deg, #d7d5cf 0%, #efeee9 45%, #96938a 60%, #7a776d 100%); }
  .photo.room-before { background: linear-gradient(180deg, var(--room-1) 0%, #f5f4f1 55%, var(--room-2) 72%, #5e4e40 100%); }
  .photo.room-after { background: linear-gradient(180deg, var(--room-3) 0%, #eeebe4 55%, var(--room-4) 75%, #4e4237 100%); }

  .tag { position: absolute; height: 36px; color: #fff; font-weight: 700; font-size: 23px; letter-spacing: .5px;
         display: flex; align-items: center; justify-content: center; border-radius: 3px; }
  .tag.before { background: var(--green); }
  .tag.after { background: var(--blue); }

  .brand { position: absolute; left: 521px; top: 125px; transform: translate(-50%, -50%);
           width: 200px; height: 200px; border-radius: 50%; background: var(--paper);
           display: flex; align-items: center; justify-content: center; }
  .brand-name { font-size: 17px; font-weight: 600; color: var(--ink); text-align: center; line-height: 1.25; letter-spacing: .3px; }

  .headline-lead { left: 52px; top: 478px; font-size: 56px; font-weight: 400; line-height: 1; }
  .headline-main { left: 50px; top: 540px; font-family: "Syne", sans-serif; font-weight: 800; color: var(--orange);
                   font-size: 84px; line-height: 80px; letter-spacing: 1px; white-space: nowrap;
                   transform: scaleX(0.86); transform-origin: left top; }
  .headline-rule { left: 52px; top: 692px; width: 450px; height: 1px; background: var(--rule); }
  .subhead { left: 57px; top: 702px; font-size: 32px; font-weight: 700; }

  .service-table { position: absolute; top: 751px; width: 264px; height: 237px; border: 1.5px solid var(--ink);
                   border-radius: 4px; overflow: hidden; display: flex; flex-direction: column; }
  .service-table .head { height: 47px; color: #fff; font-weight: 700; font-size: 14.5px; display: flex; align-items: center; padding-left: 11px; flex: none; }
  .service-table.epoxy .head { background: var(--green); }
  .service-table.pavers .head { background: var(--blue); padding-left: 6px; }
  .service-table ul { list-style: none; flex: 1; display: flex; flex-direction: column; }
  .service-table li { flex: 1; border-top: 1px solid var(--rule); display: flex; align-items: center; font-size: 12.5px; font-weight: 500; line-height: 1.3; padding: 0 8px 0 12px; }
  .service-table.pavers li { padding-left: 6px; }
  .service-table li::before { content: ""; width: 7px; height: 7px; border-radius: 50%; margin-right: 9px; flex: none; }
  .service-table.epoxy li::before { background: var(--green); }
  .service-table.pavers li::before { background: var(--blue); }

  .practical { left: 57px; top: 1017px; font-size: 14.5px; font-weight: 700; letter-spacing: .1px; }
  .feature { position: absolute; top: 1052px; width: 180px; transform: translateX(-50%); text-align: center; font-size: 12.5px; font-weight: 500; line-height: 1.3; }
  .feature svg { display: block; margin: 0 auto 4px; }
  .divider { position: absolute; top: 1052px; width: 1px; height: 82px; background: var(--rule); }

  .cta { left: 680px; top: 1016px; width: 311px; height: 81px; background: var(--orange); color: #fff; text-align: center; padding-top: 7px; }
  .cta-label { font-size: 19px; font-weight: 500; letter-spacing: .5px; line-height: 1.2; }
  .cta-phone { font-size: 39px; font-weight: 800; line-height: 1.15; letter-spacing: .5px; }
  .cta-note { left: 680px; top: 1103px; width: 311px; text-align: center; font-size: 14px; font-weight: 700; }
</style>
</head>
<body>

  <div class="photo-frame" style="left:56px; top:117px; width:463px; height:314px;">
    <div class="photo garage-before" role="img" aria-label="Worn concrete garage floor before coating"></div>
  </div>
  <div class="photo-frame" style="left:524px; top:117px; width:463px; height:314px;">
    <div class="photo garage-after" role="img" aria-label="Clean coated garage floor after service"></div>
  </div>
  <div class="tag before" style="left:188px; top:414px; width:167px;">BEFORE</div>
  <div class="tag after" style="left:671px; top:414px; width:167px;">AFTER</div>

  <div class="brand"><div class="brand-name">HARBOR RIDGE<br>PAINTING</div></div>

  <div class="abs headline-lead">Upgrade Your</div>
  <div class="abs headline-main">Garage &amp;<br>Driveway</div>
  <div class="abs headline-rule"></div>
  <div class="abs subhead">From worn-out to like new</div>

  <div class="service-table epoxy" style="left:57px;">
    <div class="head">EPOXY FLOOR COATINGS</div>
    <ul>
      <li>Durable, long-lasting finish</li>
      <li>Slip-resistant texture</li>
      <li>Covers cracks &amp; imperfections</li>
      <li>Easy to clean &amp; maintain</li>
    </ul>
  </div>
  <div class="service-table pavers" style="left:339px;">
    <div class="head">PAVER SEALING</div>
    <ul>
      <li>Restores color &amp;<br>enhances appearance</li>
      <li>Protects from sun fading</li>
      <li>Helps prevent weeds &amp; sand loss</li>
      <li>Easier to clean &amp; maintain</li>
    </ul>
  </div>

  <div class="photo-frame" style="left:684px; top:502px; width:306px; height:469px; padding:0; background:var(--orange-frame); display:flex; flex-direction:column; gap:5px;">
    <div class="photo room-before" role="img" aria-label="Room with worn tile floor before" style="height:50%;"></div>
    <div class="photo room-after" role="img" aria-label="Room with new finished floor after" style="height:50%;"></div>
  </div>
  <div class="tag before" style="left:753px; top:482px; width:166px;">BEFORE</div>
  <div class="tag after" style="left:753px; top:954px; width:166px;">AFTER</div>

  <div class="abs practical">PRACTICAL UPGRADES THAT PROTECT AND IMPROVE YOUR HOME</div>

  <div class="feature" style="left:130px;">
    <svg width="34" height="38" viewBox="0 0 34 38" aria-hidden="true">
      <path d="M17 2 L31 7 V18 C31 27 25 33 17 36 C9 33 3 27 3 18 V7 Z" fill="none" stroke="var(--orange)" stroke-width="3"/>
      <path d="M17 8 L26 11 V18 C26 24 22 28 17 30 Z" fill="var(--orange)"/>
    </svg>
    Licensed &amp; Insured
  </div>
  <div class="divider" style="left:233px;"></div>
  <div class="feature" style="left:335px;">
    <svg width="38" height="38" viewBox="0 0 38 38" aria-hidden="true">
      <path d="M6 32 L28 10" stroke="var(--orange)" stroke-width="5" stroke-linecap="round"/>
      <circle cx="29" cy="9" r="6" fill="none" stroke="var(--orange)" stroke-width="3.5"/>
      <path d="M8 6 L32 32" stroke="var(--orange)" stroke-width="5" stroke-linecap="round"/>
      <path d="M3 8 L8 3 L12 7 L7 12 Z" fill="var(--orange)"/>
    </svg>
    Family-Owned<br>Local Business
  </div>
  <div class="divider" style="left:433px;"></div>
  <div class="feature" style="left:541px;">
    <svg width="30" height="38" viewBox="0 0 30 38" aria-hidden="true">
      <path d="M15 2 C7 2 2 8 2 15 C2 24 15 36 15 36 C15 36 28 24 28 15 C28 8 23 2 15 2 Z" fill="var(--orange)"/>
      <circle cx="15" cy="15" r="5" fill="#fff"/>
    </svg>
    Serving Maple Hollow &amp;<br>Surrounding Areas
  </div>

  <div class="abs cta">
    <div class="cta-label">CALL FOR A FREE ESTIMATE</div>
    <div class="cta-phone">928-555-0147</div>
  </div>
  <div class="abs cta-note">Fast, professional service you can trust</div>

</body>
</html>
```